BrimFalcon Business Cards

We have a defined brand. Please visit our website to get a feel for the product and the color pallets. www.brimfalcon-example.com

We need an updated, world class business card design. (See the attached existing card design). Please utilize BOTH sides of the card as shown and be creative with the layout. I do want the horse head icon to be positioned as it is with the existing card.

The remainder of the layout can be customized and I also want it vertically oriented.

Attached are the logo files and please use the colors as follows:
Green - #A5CE39
Tan - #CDBD99
Black

Feel free to play with the colors.

```html
<!DOCTYPE html>
<html lang="en">
<head>
<meta charset="utf-8">
<title>BrimFalcon Labs – Business Card</title>
<link rel="stylesheet" href="https://fonts.googleapis.com/css2?family=Lato:wght@400;700&display=swap">
<style>
  :root {
    --backdrop: #4a3224;
    --card-white: #ffffff;
    --card-dark: #222322;
    --green: #a5ce39;
    --ink: #1c1c1c;
    --grey: #7d7d7d;
  }
  * { margin: 0; padding: 0; box-sizing: border-box; }
  html, body { width: 1200px; height: 848px; overflow: hidden; }
  body {
    background: var(--backdrop);
    font-family: "Lato", Arial, sans-serif;
    position: relative;
  }
  .card {
    position: absolute;
    width: 335px;
    height: 586px;
    box-shadow: 0 6px 18px rgba(0,0,0,.35);
  }
  .card--front { left: 242px; top: 127px; background: var(--card-white); }
  .card--back  { left: 612px; top: 129px; background: var(--card-dark); }

  .brand { position: absolute; left: 33px; top: 38px; }
  .brand__row { display: flex; align-items: center; gap: 8px; }
  .brand__dot { width: 34px; height: 34px; border-radius: 50%; background: var(--ink); }
  .brand__name { font-size: 27px; font-weight: 700; color: var(--ink); letter-spacing: .3px; }
  .brand__tagline {
    margin: 6px 0 0 50px;
    font-size: 11.5px; font-weight: 700; color: var(--ink);
    letter-spacing: 2.6px;
  }

  .person { position: absolute; left: 34px; top: 384px; }
  .person__name { font-size: 21px; font-weight: 700; color: var(--green); }
  .person__title { font-size: 13.5px; color: var(--grey); margin-top: 2px; }
  .person__location { font-size: 13.5px; color: var(--grey); line-height: 19px; margin-top: 18px; }
  .contact { list-style: none; margin-top: 12px; }
  .contact__item {
    display: flex; align-items: center; gap: 6px;
    font-size: 13.5px; color: var(--grey); line-height: 19px;
  }
  .contact__icon { width: 11px; height: 11px; flex: none; }

  .emblem {
    position: absolute; left: 62px; top: 185px;
    width: 212px; height: 212px; border-radius: 50%;
    background: radial-gradient(circle at 65% 30%, #6a6a6a, #2a2a2a 60%, #111 100%);
  }
  .back__tagline {
    position: absolute; left: 0; right: 0; top: 434px;
    text-align: center; font-size: 13px; color: var(--green); letter-spacing: .4px;
  }
</style>
</head>
<body>
  <section class="card card--front">
    <div class="brand">
      <div class="brand__row">
        <span class="brand__dot"></span>
        <span class="brand__name">BrimFalcon Labs</span>
      </div>
      <p class="brand__tagline">Performance Driven EVs</p>
    </div>

    <div class="person">
      <h1 class="person__name">Dana Whitlow</h1>
      <p class="person__title">President &amp; CEO</p>
      <p class="person__location">Lakemont, Saskatchewan<br>Canada</p>
      <ul class="contact">
        <li class="contact__item">
          <svg class="contact__icon" viewBox="0 0 12 12"><path fill="#a5ce39" d="M2.5 0.5l2 2-1 1.5c.7 1.6 1.9 2.8 3.5 3.5l1.5-1 2 2-1.5 2C4.5 10.5 1.5 7.5.5 2z"/></svg>
          306.555.0148
        </li>
        <li class="contact__item">
          <svg class="contact__icon" viewBox="0 0 12 12"><rect x="0.5" y="2.5" width="11" height="7" fill="#a5ce39"/><path d="M0.5 2.5L6 7l5.5-4.5" fill="none" stroke="#fff" stroke-width="1"/></svg>
          dana@brimfalcon-example.com
        </li>
        <li class="contact__item">
          <svg class="contact__icon" viewBox="0 0 12 12"><circle cx="6" cy="6" r="5.3" fill="none" stroke="#a5ce39" stroke-width="1.3"/><path d="M0.7 6h10.6M6 .7c-2.5 3-2.5 7.6 0 10.6M6 .7c2.5 3 2.5 7.6 0 10.6" fill="none" stroke="#a5ce39" stroke-width="1"/></svg>
          brimfalconlabs-example.com
        </li>
      </ul>
    </div>
  </section>

  <section class="card card--back">
    <div class="emblem" role="img" aria-label="Large dark brand emblem area"></div>
    <p class="back__tagline">MOBILITY REIMAGINED</p>
  </section>
</body>
</html>
```